Inspirational Quotes Poster Set

Brookloft is a stylish coworking space, which has a design-oriented vintage look from the 60's with an industrial touch (www.brookloft-example.com) Brookloft Quote Poster Set of 16 posters. The poster should be typo oriented and rather simple. Reflecting a bit the clean billboard design from the sixties. Minimal / simple graphical elements

Target Market(s)

Startups and Entrepreneurs

Industry/Entity Type

Startup

Font styles to use
Sans Serif

Colors

Designer to choose colors to be used in the design.

Requirements
Must have
• Posters need to be on and very stylish

```html
<!DOCTYPE html>
<html lang="en">
<head>
<meta charset="utf-8">
<title>Brookloft Quote Poster Set</title>
<link rel="stylesheet" href="https://fonts.googleapis.com/css2?family=Archivo:wdth,wght@62..125,100..900&display=swap">
<style>
  :root {
    --ochre: #c9a20c;
    --umber: #5e4413;
    --chalk: #ffffff;
    --grid: rgba(255, 255, 255, 0.85);
  }
  html, body {
    margin: 0;
    padding: 0;
    overflow: hidden;
    background: var(--ochre);
  }
  .poster {
    position: relative;
    width: 801px;
    height: 1200px;
    overflow: hidden;
    background: var(--ochre);
    font-family: "Archivo", "Helvetica Neue", Arial, sans-serif;
    font-variation-settings: "wdth" 112;
  }
  .poster__grid,
  .poster__headline {
    position: absolute;
    inset: 0;
    width: 801px;
    height: 1200px;
  }
  .grid-line {
    stroke: var(--grid);
    stroke-width: 0.6;
  }
  .headline__lead {
    fill: var(--chalk);
    font-weight: 800;
    font-size: 63px;
  }
  .headline__punch {
    font-weight: 800;
    font-size: 132px;
  }
  .headline__punch--dark { fill: var(--umber); }
  .headline__punch--light { fill: var(--chalk); }
  .zigzag {
    fill: none;
    stroke: var(--chalk);
    stroke-width: 2;
    stroke-linejoin: miter;
  }
  .attribution {
    position: absolute;
    left: 70px;
    top: 1021px;
    margin: 0;
    color: var(--chalk);
    font-weight: 700;
    font-size: 23px;
    line-height: 27px;
    letter-spacing: -1px;
  }
  .brand {
    position: absolute;
    left: 70px;
    top: 1097px;
    margin: 0;
    color: var(--chalk);
    font-weight: 800;
    font-size: 46px;
    letter-spacing: -2.5px;
    line-height: 1;
  }
</style>
</head>
<body>
<main class="poster">
  <svg class="poster__grid" viewBox="0 0 801 1200" aria-hidden="true">
    <g>
      <line class="grid-line" x1="68" y1="0" x2="68" y2="1200"/>
      <line class="grid-line" x1="163" y1="0" x2="163" y2="1200"/>
      <line class="grid-line" x1="258" y1="0" x2="258" y2="1200"/>
      <line class="grid-line" x1="353" y1="0" x2="353" y2="1200"/>
      <line class="grid-line" x1="448" y1="0" x2="448" y2="1200"/>
      <line class="grid-line" x1="543" y1="0" x2="543" y2="1200"/>
      <line class="grid-line" x1="638" y1="0" x2="638" y2="1200"/>
      <line class="grid-line" x1="733" y1="0" x2="733" y2="1200"/>
      <line class="grid-line" x1="0" y1="78" x2="801" y2="78"/>
      <line class="grid-line" x1="0" y1="173" x2="801" y2="173"/>
      <line class="grid-line" x1="0" y1="268" x2="801" y2="268"/>
      <line class="grid-line" x1="0" y1="363" x2="801" y2="363"/>
      <line class="grid-line" x1="0" y1="458" x2="801" y2="458"/>
      <line class="grid-line" x1="0" y1="553" x2="801" y2="553"/>
      <line class="grid-line" x1="0" y1="648" x2="801" y2="648"/>
      <line class="grid-line" x1="0" y1="743" x2="801" y2="743"/>
      <line class="grid-line" x1="0" y1="838" x2="801" y2="838"/>
      <line class="grid-line" x1="0" y1="933" x2="801" y2="933"/>
      <line class="grid-line" x1="0" y1="1028" x2="801" y2="1028"/>
      <line class="grid-line" x1="0" y1="1123" x2="801" y2="1123"/>
    </g>
  </svg>

  <svg class="poster__headline" viewBox="0 0 801 1200" role="img"
       aria-label="insanity is doing the same thing over and over again and expecting different results">
    <defs>
      <clipPath id="above-zigzag">
        <polygon points="0,0 801,0 801,603 733,478 638,553 448,382 227,628 68,437 0,522"/>
      </clipPath>
    </defs>

    <g class="headline__lead">
      <text x="58" y="249" textLength="516" lengthAdjust="spacingAndGlyphs">insanity is doing</text>
      <text x="57" y="310" textLength="486" lengthAdjust="spacingAndGlyphs">the same thing</text>
      <text x="57" y="373" textLength="650" lengthAdjust="spacingAndGlyphs">over &amp; over again&#160;&#160;&amp;</text>
    </g>

    <g class="headline__punch headline__punch--dark">
      <text x="60" y="515" textLength="661" lengthAdjust="spacingAndGlyphs">expecting</text>
      <text x="61" y="642" textLength="600" lengthAdjust="spacingAndGlyphs">different</text>
      <text x="64" y="770" textLength="469" lengthAdjust="spacingAndGlyphs">results</text>
    </g>

    <g class="headline__punch headline__punch--light" clip-path="url(#above-zigzag)" aria-hidden="true">
      <text x="60" y="515" textLength="661" lengthAdjust="spacingAndGlyphs">expecting</text>
      <text x="61" y="642" textLength="600" lengthAdjust="spacingAndGlyphs">different</text>
      <text x="64" y="770" textLength="469" lengthAdjust="spacingAndGlyphs">results</text>
    </g>

    <polyline class="zigzag" points="0,522 68,437 227,628 448,382 638,553 733,478 801,603"/>
  </svg>

  <p class="attribution">Alfred Eberstein,<br>Physicist</p>
  <p class="brand">Brookloft</p>
</main>
</body>
</html>
```